Website development company website

ABOUT COMPANY
Hi everyone! We're a Melbourne, Australia website development company in a need of a website design that will make online store merchants want to engage our services.
We specialise exclusively in Torvista e-commerce platform (https://torvista-platform.example/). What distinguishes our business from competition is that rather than designing and building brand new websites, we offer development, support and maintenance services to established websites. Maintenance and Support are the keywords representing our business.
Our potential clients are people with broken, slow and underperforming Torvista installations who need assistance getting their websites up and making sales. Our website must pass the message that we can help, and provide quick means of making contact.
DESIGN
Overall, we're looking for a slick, clean, airy, conservative design. No need to do anything crazy, try to stick to what's "standard" in website design these days and make it easy on all of us. The website is unlikely to be updated too often so it needs to look attractive and fresh first time over and after a year, too.
Attached is our new logo, which you'll be able to take the basic idea from, the colors and fonts. Though, don't use the fonts from the logo in the website, stick to the standard widely supported fonts. Additional use of Google fonts is fine.
Don't overdo it with colors, stick to conservative basic color set and only use the colors from the log for accents like headings etc. Please, don't be tempted to use the blue and orange as background of whole blocks, other than perhaps footer. Thanks.
For the images used, I'd like to stay away from a design studio/digital agency feel and lean more towards professional support and maintenance services. I'm thinking images of content merchants doing their job. Something along the lines of "We'll be taking care of the website so that you only need to care about the business".
Some ideas I like:
http://www.plumframe-pics.example/detail/photo/portrait-of-confident-male-design-professional-royalty-free-image/572048163
http://www.plumframe-pics.example/detail/photo/designer-taking-picture-of-hat-high-res-stock-photography/839207514
http://www.plumframe-pics.example/detail/photo/woman-packaging-pottery-royalty-free-image/216684093
Images of colorful shopping bags and shopping carts are over the top and not serious enough. Instead of images matching Online Shopping, I'd try going more for Stability, Reliability, Performance.
Our existing website is http://www.bravuln.example. Please, don't take design ideas from it, but it will give you a picture of the structure of our new website and content that's going to be used initially.
If you could include a basic icon set to use throughout the website, that would be great. If the icons could match our logo (attached), it would be a big plus.
ALL PAGES
Every page must contain clearly visible phone number (1300 648 907) and a Contact Us Now button, which opens an AJAX driven popup form with Name, Email, Phone and Message to be sent through.
To start with, main menu items will be Torvista, Portfolio, Contact.
At the bottom of each page, please, include a newsletter subscription form with text Subscribe to Torvista Support and Security Updates.
For the footer, I'd like to see a logo strip with the following logos in grayscale (no need to link anywhere): Torvista, QRX, DataVane, NCB. You'll find the logos on Google Images.
Standard footer columns follow. Here, I'd like to see logos in color: Torvista Certified Developer, Torvista Ceritified Solution Provider. Again, the logos are on Google Images.
No social media logos/links necessary anywhere on the website.
...and then the copyright line.
FRONT PAGE
Large slider with images that would appeal to our target audience. Keywords here would be Torvista System Audit, Torvista Performance Optimisation, Torvista Website Emergency Recovery, Torvista Development Infrastructure Hosting. We'll have a static page created for each of these to link to.
In a corner of the slider, or on the edge, can I have an overlay with logos in color (same as footer): Torvista Certified Developer, Torvista Ceritified Solution Provider.
Underneath, a number of blocks, each with an image and teaser that we'll use to link to various pages throughout the website.
PORTFOLIO PAGE
I'm thinking a single long page with a block per client, which will contain project name, description from us and a testimonial from client. Also, each block will contain a single large screenshot. No gallery or slideshow is necessary here, just one image per project.
I'll leave the layout up to you, but try to put yourself in the shoes of a potential client reviewing our past work by simply scrolling down this one page.
CONTACT US PAGE
Separate page with the same form as above, phone number (1300 648 907), email address (support@kavreo.example), address (Suite 42, Level 3|8 Wattlebrook Lane|Fernvale Heights VIC 3999), and a grayscale Google Map.
CODING UP
Coding up into static HTML/CSS/JS is equally important as the design itself. We're a website development company, we'll be integrating the theme. We will spot any issues and we will point them out.
Coded up design must be fully responsive. Enough said.
To be able to create any content in future, we'd like one extra page coded up with samples of all themed elements, lists, forms, buttons, 2, 3, 4-column layout, alerts, icons, etc. This page does not need to be designed, only coded up.
The design will be integrated into Drupal using Twig. If possible at all, try to keep it in mind when designing and coding up, and make the integration into a Drupal theme easier for us.
GOOD LUCK!
That's it. Let me know if anything needs clarifying. So far I've had a great experience with ArtFlockly. I don't doubt some great designs will emerge. Clever ideas are highly appreciated, but also make it clear you've read and followed the points in this brief. Cheers, Tom

```html
<!DOCTYPE html>
<html lang="en">
<head>
<meta charset="utf-8">
<title>Bravuln – Torvista Support &amp; Development</title>
<link rel="stylesheet" href="https://fonts.googleapis.com/css2?family=Open+Sans:ital,wght@0,400;0,600;0,700;1,400&display=swap">
<style>
:root{
  --orange:#e07b24;
  --orange-dark:#c9661a;
  --navy:#1d3f73;
  --ink:#333333;
  --muted:#7a7a7a;
  --line:#e3e3e3;
  --soft:#f3f3f1;
  --footer:#262626;
  --footer-base:#1b1b1b;
  --footer-text:#9a9a9a;
  --white:#ffffff;
}
*{box-sizing:border-box;margin:0;padding:0}
html,body{width:1200px;height:2390px;overflow:hidden}
body{font-family:"Open Sans",Arial,sans-serif;color:var(--ink);background:var(--white);position:relative}
a{color:inherit;text-decoration:none}

/* Hero */
.hero{position:absolute;left:0;top:0;width:1200px;height:603px;overflow:hidden}
.hero-photo{position:absolute;inset:0;background:
  radial-gradient(ellipse at 30% 45%,#cfd3d8 0,#8d949c 14%,rgba(40,40,48,0) 34%),
  radial-gradient(ellipse at 75% 60%,rgba(214,150,70,.55) 0,rgba(30,28,34,0) 40%),
  linear-gradient(180deg,#15171d 0%,#22242c 55%,#3a2e24 100%)}
.brand{position:absolute;left:99px;top:50px;display:flex;align-items:center;gap:12px;color:var(--orange);font-weight:700;font-size:34px;letter-spacing:-.5px}
.brand-square{width:34px;height:40px;background:var(--orange)}
.topbar{position:absolute;right:99px;top:24px;display:flex;gap:24px;color:var(--white);font-size:13px;align-items:center}
.topbar span{display:flex;align-items:center;gap:9px}
.contact-now{height:30px;line-height:30px;padding:0 14px;font-size:11.5px}
.nav{position:absolute;right:99px;top:76px;display:flex;align-items:center;font-size:11.5px;font-weight:600;color:var(--white)}
.nav a{margin-left:58px}
.nav a.active{color:var(--orange)}
.search{margin-left:38px;width:36px;height:36px;border-radius:50%;background:#b05a1b;display:flex;align-items:center;justify-content:center}
.hero-copy{position:absolute;right:99px;top:242px;text-align:right;color:var(--white)}
.hero-kicker{font-size:19px;font-weight:600;letter-spacing:.5px}
.hero-title{font-size:41px;font-weight:700;letter-spacing:1px;margin-top:6px}
.btn{display:inline-block;background:linear-gradient(#e8862c,#d46d17);color:var(--white);font-size:12.5px;font-weight:600;text-transform:uppercase;border-radius:3px;text-align:center}
.hero-btn{position:absolute;right:99px;top:341px;width:125px;height:46px;line-height:42px;border:2px solid var(--white);font-size:13px}
.badges{position:absolute;right:99px;top:459px;display:flex;gap:14px}
.badge{width:68px;height:104px;border:1px solid #cfcfcf;padding:6px}
.badge i{display:block;width:100%;height:100%;background:linear-gradient(#e07b24 0 55%,#dcdcdc 55%)}
.badge.alt i{background:linear-gradient(#f2f2f2 0 55%,#b9b9b9 55%)}
.dots{position:absolute;left:861px;top:549px;display:flex;gap:10px}
.dots i{width:16px;height:16px;border-radius:50%;background:var(--white);position:relative}
.dots i.on{background:transparent;border:2px solid var(--orange)}
.dots i.on::after{content:"";position:absolute;left:3px;top:3px;width:6px;height:6px;border-radius:50%;background:var(--orange)}

/* Section heads */
.section-title{position:absolute;left:0;width:1200px;text-align:center;font-size:25px;font-weight:600;color:var(--ink);display:flex;justify-content:center;align-items:center;gap:12px}
.section-title i{width:20px;height:26px;background:var(--orange);border-bottom:6px solid var(--navy)}
.section-lead{position:absolute;left:160px;width:880px;text-align:center;font-size:12px;line-height:20px;color:var(--muted)}

/* Service cards */
.card{position:absolute;top:917px;width:312px;height:282px;border:1px solid var(--line);text-align:center}
.card-icon{position:absolute;left:50%;top:-100px;margin-left:-66px;width:132px;height:132px;border-radius:50%;background:var(--navy);display:flex;align-items:center;justify-content:center;box-shadow:8px 0 0 var(--orange)}
.card-title{position:absolute;top:100px;width:100%;color:var(--orange);font-size:14px;font-weight:700}
.card-text{position:absolute;top:128px;left:22px;right:22px;font-size:12px;line-height:22px;color:var(--muted)}
.card .btn{position:absolute;left:94px;top:207px;width:122px;height:42px;line-height:42px}
.divider{position:absolute;left:99px;top:1245px;width:1002px;height:1px;background:#d6d6d6}

/* Work */
.work-tile{position:absolute;top:1392px;width:248px;height:165px}
.work-caption{position:absolute;top:1574px;width:248px;text-align:center}
.work-caption h3{font-size:14px;font-weight:600;line-height:22px;text-transform:uppercase;color:var(--ink)}
.work-caption p{font-size:10.5px;font-style:italic;color:var(--orange);margin-top:3px}

/* Testimonials */
.testimonials{position:absolute;left:0;top:1678px;width:1200px;height:287px;background:
  radial-gradient(ellipse at 42% 45%,rgba(255,255,255,.9) 0,rgba(243,243,241,0) 32%),
  linear-gradient(90deg,#ecebe8,var(--soft) 50%,#e9e8e5);border-top:1px solid var(--line)}
.testimonials .section-title{top:73px}
.quote{position:absolute;top:143px;width:1200px;text-align:center;color:#555;font-size:12.5px;font-style:italic;line-height:23px}
.quote .mark{font-size:26px;vertical-align:-8px;margin:0 4px;color:var(--orange)}
.arrow{position:absolute;top:168px}

/* Logo strip */
.logo-strip{position:absolute;left:0;top:1967px;width:1200px;height:118px;border-bottom:3px solid var(--orange)}
.logo-cell{position:absolute;top:0;height:115px;display:flex;align-items:center;justify-content:center;color:#555;font-size:30px;font-weight:600}
.logo-sep{position:absolute;top:0;width:1px;height:115px;background:var(--line)}

/* Footer */
.footer{position:absolute;left:0;top:2088px;width:1200px;height:231px;background:var(--footer);color:var(--footer-text)}
.footer-brand{position:absolute;left:99px;top:40px;display:flex;align-items:center;gap:10px;color:#8a8a8a;font-size:32px;font-weight:700}
.footer-brand i{width:30px;height:38px;background:#6f6f6f}
.newsletter{position:absolute;left:99px;top:104px;width:240px}
.newsletter p{font-size:11.5px;line-height:17px;color:#bdbdbd}
.newsletter form{display:flex;margin-top:10px}
.newsletter span.field{flex:1;height:32px;line-height:32px;padding:0 10px;background:#3a3a3a;border:1px solid #4a4a4a;font-size:11px;color:#8a8a8a}
.newsletter .btn{height:32px;line-height:32px;padding:0 12px;font-size:11px;border-radius:0 3px 3px 0}
.footer h4{position:absolute;top:44px;color:var(--white);font-size:13.5px;font-weight:600}
.footer-nav{position:absolute;left:372px;top:80px;list-style:none;font-size:10.5px;line-height:25.5px}
.footer-nav li::before{content:"›";margin-right:9px;color:#888}
.footer-contact{position:absolute;left:524px;top:80px;width:240px;list-style:none;font-size:10.5px;line-height:17px;text-transform:uppercase}
.footer-contact li{display:flex;gap:10px;margin-bottom:12px}
.footer-contact svg{flex:none;margin-top:2px}
.map{position:absolute;left:784px;top:40px;width:316px;height:147px;border:2px solid #444;background:linear-gradient(135deg,#dcdcdc,#c4c4c4 50%,#d6d6d6)}
.base{position:absolute;left:0;top:2319px;width:1200px;height:71px;background:var(--footer-base);color:var(--white);font-size:11px;font-weight:600}
.base .copy{position:absolute;left:99px;top:28px}
.base .support{position:absolute;right:99px;top:17px;display:flex;align-items:center;gap:6px}
.mini-badge{width:22px;height:36px;border:1px solid #aaa;padding:2px}
.mini-badge i{display:block;width:100%;height:100%;background:linear-gradient(var(--orange) 0 55%,#ccc 55%)}
</style>
</head>
<body>

<header class="hero">
  <div class="hero-photo" role="img" aria-label="Hands typing on a laptop in front of a city skyline at night"></div>
  <a class="brand" href="#"><span class="brand-square"></span>Kavreo</a>
  <div class="topbar">
    <span><svg width="18" height="18" viewBox="0 0 24 24" fill="none" stroke="#fff" stroke-width="1.6"><path d="M5 3h4l2 5-3 2a11 11 0 0 0 6 6l2-3 5 2v4a2 2 0 0 1-2 2A17 17 0 0 1 3 5a2 2 0 0 1 2-2z"/></svg>PHONE: 1300 648 907</span>
    <span><svg width="20" height="15" viewBox="0 0 24 18" fill="none" stroke="#fff" stroke-width="1.6"><rect x="1" y="1" width="22" height="16"/><path d="M1 1l11 9 11-9"/></svg>MAIL: support@kavreo.example</span>
    <a class="btn contact-now" href="#">Contact Us Now</a>
  </div>
  <nav class="nav">
    <a class="active" href="#">TORVISTA</a><a href="#">PORTFOLIO</a><a href="#">CONTACT</a>
    <span class="search"><svg width="13" height="13" viewBox="0 0 24 24" fill="none" stroke="#fff" stroke-width="3"><circle cx="10" cy="10" r="7"/><path d="M15 15l7 7"/></svg></span>
  </nav>
  <div class="hero-copy">
    <div class="hero-kicker">TORVISTA DEVELOPMENT</div>
    <div class="hero-title">INFRASTRUCTURE</div>
  </div>
  <a class="btn hero-btn" href="#">Read More</a>
  <div class="badges">
    <div class="badge"><i></i></div>
    <div class="badge alt"><i></i></div>
  </div>
  <div class="dots"><i class="on"></i><i></i><i></i></div>
</header>

<section class="welcome">
  <h2 class="section-title" style="top:650px"><i></i>WELCOME TO BRAVULN</h2>
  <p class="section-lead" style="top:705px">Sed ut perspiciatis unde omnis iste natus error sit voluptatem accusantium doloremque laudantium, totam rem aperiam, eaque ipsa quae ab illo inventore veritatis et quasi architecto beatae vitae dicta sunt explicabo. Nemo enim ipsam voluptatem quia voluptas sit aspernatur aut odit aut fugit, sed quia consequuntur magni dolores eos qui ratione voluptatem sequi nesciunt...</p>

  <article class="card" style="left:99px">
    <div class="card-icon"><svg width="58" height="58" viewBox="0 0 60 60" fill="none" stroke="#fff" stroke-width="3"><circle cx="30" cy="30" r="27"/><path d="M18 30l12-12h12v12L30 42z"/><circle cx="36" cy="24" r="2.5"/></svg></div>
    <h3 class="card-title">WHY BRAVULN?</h3>
    <p class="card-text">Fast Torvista-based online stores, built on time and to specification, backed by effective, focused support, means that our clients...</p>
    <a class="btn" href="#">Read More</a>
  </article>
  <article class="card" style="left:444px">
    <div class="card-icon"><svg width="58" height="58" viewBox="0 0 60 60" fill="none" stroke="#fff" stroke-width="3"><circle cx="30" cy="30" r="27"/><rect x="17" y="20" width="26" height="20"/><path d="M19 37l8-8 6 6 4-4 5 5"/><circle cx="36" cy="25" r="2"/></svg></div>
    <h3 class="card-title">WHY TORVISTA?</h3>
    <p class="card-text">Torvista is the world's leading open source eCommerce platform. No other open-source or free system offers...</p>
    <a class="btn" href="#">Read More</a>
  </article>
  <article class="card" style="left:789px">
    <div class="card-icon"><svg width="58" height="58" viewBox="0 0 60 60" fill="none" stroke="#fff" stroke-width="3"><circle cx="30" cy="30" r="27"/><rect x="19" y="20" width="22" height="15"/><path d="M15 39h30"/></svg></div>
    <h3 class="card-title">WHAT WE DO</h3>
    <p class="card-text">From support, maintenance and upgrades to redesigns, migrations and full site builds, we make your online...</p>
    <a class="btn" href="#">Read More</a>
  </article>
</section>

<div class="divider"></div>

<section class="work">
  <h2 class="section-title" style="top:1292px"><i></i>OUR WORK</h2>
  <p class="section-lead" style="top:1341px">Veritatis et quasi architecto beatae vitae dicta sunt explicabo. Nemo enim ipsam voluptatem quia voluptas sit aspernatur</p>

  <div class="work-tile" style="left:99px;background:linear-gradient(135deg,#6a4a34,#b99a82 55%,#e6e0da)" role="img" aria-label="Developer reviewing code on a monitor"></div>
  <div class="work-tile" style="left:350px;background:linear-gradient(135deg,#f1e6d6,#d9b88e 60%,#c79b6a)" role="img" aria-label="Hands reviewing printed performance charts"></div>
  <div class="work-tile" style="left:601px;background:linear-gradient(135deg,#1a4a80,#3b78b8 55%,#8fb9de)" role="img" aria-label="Businessman touching an internal control screen"></div>
  <div class="work-tile" style="left:852px;background:linear-gradient(135deg,#e9eef2,#a9bccb 55%,#47657f)" role="img" aria-label="Several screens showing website layouts"></div>

  <div class="work-caption" style="left:99px"><h3>Torvista System<br>Audit</h3><p>Click View More Information</p></div>
  <div class="work-caption" style="left:350px"><h3>Torvista Performance<br>Optimisation</h3><p>Click View More Information</p></div>
  <div class="work-caption" style="left:601px"><h3>Website<br>Emergency Recovery</h3><p>Click View More Information</p></div>
  <div class="work-caption" style="left:852px"><h3>Torvista Development<br>Infrastructure Hosting</h3><p>Click View More Information</p></div>
</section>

<section class="testimonials" aria-label="Client testimonials">
  <h2 class="section-title"><i></i>TESTIMONIALS</h2>
  <div class="quote">
    Lacewell Lane-Nova<br>
    <span class="mark">“</span>A fast solution is key when you are selling online. Bravuln are now our go to Torvista developers, very happy<span class="mark">”</span><br>
    -Reid Calloway, Nova
  </div>
  <svg class="arrow" style="left:98px" width="10" height="14" viewBox="0 0 10 14"><path d="M8 1L2 7l6 6" fill="none" stroke="#555" stroke-width="2.5"/></svg>
  <svg class="arrow" style="left:1092px" width="10" height="14" viewBox="0 0 10 14"><path d="M2 1l6 6-6 6" fill="none" stroke="#555" stroke-width="2.5"/></svg>
</section>

<section class="logo-strip">
  <div class="logo-cell" style="left:99px;width:250px">Torvista</div>
  <div class="logo-sep" style="left:349px"></div>
  <div class="logo-cell" style="left:349px;width:249px">QRX</div>
  <div class="logo-sep" style="left:598px"></div>
  <div class="logo-cell" style="left:598px;width:252px">DataVane</div>
  <div class="logo-sep" style="left:850px"></div>
  <div class="logo-cell" style="left:850px;width:251px">NCB</div>
</section>

<footer class="footer">
  <div class="footer-brand"><i></i>Kavreo</div>
  <div class="newsletter">
    <p>Subscribe to Torvista Support and Security Updates</p>
    <form><span class="field">Your email address</span><span class="btn">Subscribe</span></form>
  </div>

  <h4 style="left:370px">NAVIGATION</h4>
  <ul class="footer-nav">
    <li>TORVISTA</li><li>PORTFOLIO</li><li>CONTACT</li>
  </ul>

  <h4 style="left:524px">CONTACT US</h4>
  <ul class="footer-contact">
    <li><svg width="10" height="13" viewBox="0 0 10 14"><path d="M5 0a5 5 0 0 1 5 5c0 4-5 9-5 9S0 9 0 5a5 5 0 0 1 5-5z" fill="#8a8a8a"/><circle cx="5" cy="5" r="2" fill="#262626"/></svg><span>Suite 42, Level 3|8 Wattlebrook<br>Lane|Fernvale Heights VIC 3999</span></li>
    <li><svg width="12" height="12" viewBox="0 0 24 24"><path d="M5 3h4l2 5-3 2a11 11 0 0 0 6 6l2-3 5 2v4a2 2 0 0 1-2 2A17 17 0 0 1 3 5a2 2 0 0 1 2-2z" fill="#8a8a8a"/></svg><span>Phone: 1300 648 907</span></li>
    <li><svg width="13" height="10" viewBox="0 0 24 18" fill="none" stroke="#8a8a8a" stroke-width="2"><rect x="1" y="1" width="22" height="16"/><path d="M1 1l11 9 11-9"/></svg><span>support@kavreo.example</span></li>
  </ul>

  <div class="map" role="img" aria-label="Grayscale street map showing the office location"></div>
</footer>

<div class="base">
  <div class="copy">COPYRIGHTS©BRAVULN.2016 | ALLRIGHTS RESERVED.</div>
  <div class="support">TORVISTA SUPPORT: <span class="mini-badge"><i></i></span><span class="mini-badge"><i></i></span></div>
</div>

</body>
</html>
```